Marigold Synchronized Swim Team's Clubhouse (web page)

Fun, Super Easy to read and navigate. Please error on the side of too large font sizes rather than too small font sizes.

We are a New Orleans (USA) based club for adults and youth of all genders.

We have youth and adult performance and competition teams. We teach synchronized swimming. We perform at special events.

Webpage should allow for

1. Sign up for classes, camps and teams (pay fees, sign waivers, reserve a spot and link to national Delmar Aquaform club membership website in order to buy required national membership).Make our multi step registration process easy, quick, pleasant.

2. Provide an area to upload practice schedules.
and performance calendar.

3. Easily
Hire one of our synchro squad to perform at special events.

4. Embedded Google Calndar

5 Members only site
( one away for youth and one area for adults. )

6 Show off our new logo, photos and videos. Be able to change these images often.

Our team colors are red, aqua and pink.

7. Buy logo gear

Click to team shop at
Brindle cove.com and other future team shops.

8. One click to become a sponsor of the team.

An area to show off sponsor logos. We will have several levels of sponsorships. It is important to have small medium and large logo spots. WE also will have a wall of names of folks who donate 10 - 100 dollars to sponsor the team.

We want the experience to be fun . We do not want headache producing events.

Our team colors are red, pink and aqua. WE have not settled on a specific red or pink yet. You are free to play around with different tones and hues. I tend toward a sholcking pink and cherry red. But really do want to see what your thoughts are for our reds and pinks. Also feel free to vary aqua from a light to dark. But we do want to stay away from navy.
Thanks for your hard work and creativity.

Target Market(s)

All ages, genders and ethnicity. Swimmers, dancers and event planners.

Coding

Coded - Design and coding required

Number of Pages Required

4 page

Font styles to use
Sans Serif

Colors
ec1f27
0293ce
f59195

Requirements
Must have
• See p descriptions +
• Fine #20 is our logo and
• Playful, bold, elegant, Colorful (red, aqua and pink are our team colors).
• I want to be able to plug in / update photos , schedules, release forms, almost everything as our seasons change. I do not know ( Newbury) do I want coded or incised site. All advice welcome.
Nice to have
• Your flare as a designer. Thank you for making us better through your creativity, ability to edit, clarify and advice. :-)
Should not have
• Confusion.

```html
<!DOCTYPE html>
<html lang="en">
<head>
<meta charset="utf-8">
<title>Marigold Synchronized Swim Team – Clubhouse</title>
<link rel="stylesheet" href="https://fonts.googleapis.com/css2?family=Montserrat:wght@400;600;700&family=Open+Sans:wght@400;600;700&display=swap">
<style>
:root{
  --red:#e1363a;
  --blue:#0b8fd2;
  --pink:#f59195;
  --ink:#4a4a4a;
  --dark:#222;
  --muted:#8a8a8a;
  --line:#e4e4e4;
  --soft:#f7f7f7;
  --star:#f5a623;
  --white:#fff;
}
*{box-sizing:border-box;margin:0;padding:0}
html,body{width:1200px;height:3750px;overflow:hidden;background:var(--white)}
body{font-family:"Open Sans",Arial,sans-serif;color:var(--ink);position:relative}
.abs{position:absolute}
h1,h2,h3,.heading{font-family:"Montserrat",Arial,sans-serif}

/* nav */
.site-nav{position:absolute;top:0;left:0;width:1200px;height:105px;background:var(--white);z-index:2}
.nav-link{position:absolute;top:56px;font-size:12px;font-weight:600;color:#555;letter-spacing:.3px}
.nav-link.active{color:var(--dark)}
.nav-link.active::after{content:"";position:absolute;left:-6px;right:-6px;top:22px;height:3px;background:var(--red)}
.brand-tab{position:absolute;left:510px;top:0;width:180px;height:180px;background:var(--white);border-radius:0 0 90px 90px;z-index:3;display:flex;flex-direction:column;align-items:center;justify-content:center;padding-top:30px;gap:10px}
.brand-mark{width:22px;height:22px;background:var(--blue);border-radius:4px}
.brand-name{font-family:"Montserrat",sans-serif;font-weight:700;font-size:17px;color:var(--blue);letter-spacing:1px}

/* hero */
.hero{position:absolute;top:105px;left:0;width:1200px;height:470px}
.hero-photo{position:absolute;inset:0;background:linear-gradient(100deg,#0c3f7a 0%,#1d74b8 35%,#3aa3d8 60%,#1a5d9c 100%)}
.hero-title{position:absolute;left:202px;top:110px;font-size:38px;line-height:42px;font-weight:700;color:var(--white)}
.hero-text{position:absolute;left:202px;top:235px;width:380px;font-size:14px;line-height:22px;color:var(--white)}
.btn{display:flex;align-items:center;justify-content:center;background:var(--blue);color:var(--white);font-family:"Montserrat",sans-serif;font-weight:700;font-size:14px;letter-spacing:.5px}
.hero-btn{position:absolute;left:202px;top:332px;width:168px;height:48px}
.slide-dots{position:absolute;left:1149px;top:203px;display:flex;flex-direction:column;gap:11px}
.slide-dot{width:11px;height:11px;background:var(--white);transform:rotate(45deg)}
.slide-dot.current{background:var(--red)}

/* upload bar */
.upload-bar{position:absolute;top:628px;left:200px;width:800px;height:42px}
.upload-field{position:absolute;top:0;height:42px;border:1px solid var(--line);font-size:11px;color:var(--muted);display:flex;align-items:center;padding:0 14px;justify-content:space-between}
.upload-btn{position:absolute;left:658px;top:0;width:140px;height:42px;background:var(--red);font-size:11px}

/* hire */
.hire-title{position:absolute;left:202px;top:765px;width:380px;font-size:42px;line-height:45px;font-weight:700;color:#4d4d4d}
.hire-btn{position:absolute;left:202px;top:975px;width:168px;height:50px;font-size:13px}
.hire-divider{position:absolute;left:607px;top:725px;width:1px;height:387px;background:var(--line)}
.event-photo{position:absolute;left:622px;top:760px;width:376px;height:202px;background:linear-gradient(180deg,#b7483c 0%,#c2332f 55%,#7a1c1c 100%)}
.event-date{position:absolute;left:622px;top:982px;font-size:12px;font-weight:700;color:var(--red)}
.event-meta{position:absolute;left:622px;top:1012px;font-size:10px;color:#444}
.event-text{position:absolute;left:622px;top:1036px;width:360px;font-size:11px;line-height:19px;color:var(--muted)}

/* members */
.members-band{position:absolute;top:1120px;left:0;width:1200px;height:375px;background:var(--red)}
.member-photo{position:absolute;top:83px;width:200px;height:200px;border-radius:50%;border:4px solid rgba(255,255,255,.5)}
.member-photo.young{left:250px;background:linear-gradient(135deg,#e9c6b0,#5aa3c4)}
.member-photo.adult{left:750px;background:linear-gradient(135deg,#2c2c3a,#b94a6a)}
.member-label{position:absolute;top:305px;width:200px;text-align:center;font-size:15px;font-weight:700;color:var(--white)}
.members-title{position:absolute;left:450px;top:145px;width:300px;text-align:center;font-size:44px;line-height:46px;font-weight:700;color:var(--white)}

/* sections */
.section-title{position:absolute;left:0;width:1200px;text-align:center;font-size:34px;font-weight:700;color:#4a4a4a}
.section-rule{position:absolute;left:200px;width:800px;height:1px;background:var(--line)}

/* news */
.news-card{position:absolute;top:1678px;width:252px}
.news-photo{width:252px;height:140px;position:relative;background:linear-gradient(160deg,#2fb8a9,#1c8b7a 60%,#5bc7b2)}
.news-date{position:absolute;left:6px;top:6px;width:42px;height:42px;background:var(--red);color:var(--white);font-size:9px;font-weight:700;line-height:12px;text-align:center;padding-top:3px}
.play{position:absolute;left:106px;top:50px;width:40px;height:40px;border-radius:50%;background:rgba(60,60,60,.75)}
.play::after{content:"";position:absolute;left:16px;top:12px;border-left:12px solid var(--white);border-top:8px solid transparent;border-bottom:8px solid transparent}
.news-head{margin-top:37px;font-size:12px;line-height:17px;font-weight:700;color:var(--dark)}
.news-body{margin-top:12px;font-size:10px;line-height:15px;color:var(--muted)}

/* gear */
.gear-section{position:absolute;top:2012px;left:0;width:1200px;height:763px;background:var(--soft)}
.gear-card{position:absolute;top:158px;width:252px;text-align:center}
.gear-photo{width:252px;height:273px;background:var(--white);border:1px solid var(--line);display:flex;align-items:center;justify-content:center}
.gear-item{width:130px;height:210px;border-radius:40px}
.gear-name{margin-top:42px;font-size:15px;font-weight:700;color:var(--red)}
.gear-type{margin-top:4px;font-size:11px;color:#555}
.gear-price{margin-top:8px;font-size:26px;color:#8a8a8a}
.gear-stars{margin-top:2px;font-size:13px;letter-spacing:3px;color:var(--star)}
.gear-stars span{color:#ccc}
.gear-store{margin-top:12px;font-family:"Montserrat",sans-serif;font-size:13px;font-weight:700;color:var(--dark)}
.gear-btn{margin:14px auto 0;width:118px;height:40px;font-size:12px}

/* sponsors */
.sponsor-row{position:absolute;top:2895px;left:200px;width:800px;display:flex;justify-content:space-between;align-items:center}
.sponsor-name{font-family:"Montserrat",sans-serif;font-size:22px;font-weight:700;color:#3a3a3a}

/* donors */
.donor-section{position:absolute;top:3000px;left:0;width:1200px;height:500px;background:var(--soft)}
.donor{position:absolute;top:128px;width:200px;text-align:center}
.donor-photo{margin:0 auto;width:122px;height:122px;border-radius:50%;border:4px solid #ddd;background:linear-gradient(160deg,#d9d9d9,#a9b4bd)}
.donor-name{margin-top:28px;font-size:15px;font-weight:700;color:var(--red)}
.donor-team{margin-top:6px;font-size:11px;font-weight:700;color:var(--dark)}
.donor-amount{margin-top:8px;font-size:22px;color:#666}
.sponsor-btn{position:absolute;left:468px;top:390px;width:265px;height:44px;font-size:15px}

/* footer */
.site-footer{position:absolute;top:3500px;left:0;width:1200px;height:250px;background:var(--white)}
.footer-brand{position:absolute;left:242px;top:60px;display:flex;align-items:center;gap:8px}
.footer-brand .brand-mark{width:16px;height:16px}
.footer-brand .brand-name{font-size:14px}
.footer-col{position:absolute;top:50px;font-size:10px;line-height:21px;color:#444;text-transform:uppercase}
.footer-about{left:385px;width:200px}
.footer-about p{text-transform:none;font-size:9px;line-height:15px;color:var(--muted);margin-top:12px}
.footer-social{position:absolute;left:900px;top:56px;display:flex;gap:9px}
.social-dot{width:12px;height:12px;border-radius:50%;background:var(--red)}
.social-dot.grey{background:#888}
.calendar-badge{position:absolute;left:890px;top:82px;width:108px;height:50px;border:1px solid var(--line);display:flex;align-items:center;gap:8px;padding:0 8px;font-size:11px;color:#444}
.calendar-badge i{width:30px;height:30px;background:var(--blue);display:block}
.footer-rule{position:absolute;left:0;top:206px;width:1200px;height:1px;background:var(--line)}
.copyright{position:absolute;top:220px;width:1200px;text-align:center;font-size:10px;color:#777}
</style>
</head>
<body>

<nav class="site-nav">
  <span class="nav-link active" style="left:250px">HOME</span>
  <span class="nav-link" style="left:322px">ABOUT US</span>
  <span class="nav-link" style="left:416px">SERVICES</span>
  <span class="nav-link" style="left:740px">MEMBERS</span>
  <span class="nav-link" style="left:830px">SCHEDULES</span>
  <span class="nav-link" style="left:932px">CONTACT US</span>
</nav>
<div class="brand-tab">
  <span class="brand-mark"></span>
  <span class="brand-name">MARIGOLD</span>
</div>

<section class="hero">
  <div class="hero-photo" role="img" aria-label="Underwater photo of a synchronized swimmer gliding through a pool"></div>
  <h1 class="hero-title">Sign Up For Classes,<br>Camps &amp; Teams</h1>
  <p class="hero-text">Pay fees, sign waivers, reserve a spot and link to national Delmar Aquaform club membership website in order to buy required national membership.</p>
  <a class="btn hero-btn">SIGN UP</a>
  <div class="slide-dots">
    <span class="slide-dot current"></span><span class="slide-dot"></span><span class="slide-dot"></span><span class="slide-dot"></span>
  </div>
</section>

<form class="upload-bar">
  <div class="upload-field" style="left:0;width:315px">Practice Schedules
    <svg width="12" height="12" viewBox="0 0 12 12"><circle cx="6" cy="6" r="4" fill="none" stroke="#0b8fd2" stroke-width="2"/></svg></div>
  <div class="upload-field" style="left:330px;width:315px">Performance Calendar
    <svg width="12" height="12" viewBox="0 0 12 12"><rect x="1" y="2" width="10" height="9" fill="none" stroke="#0b8fd2" stroke-width="1.5"/><line x1="1" y1="5" x2="11" y2="5" stroke="#0b8fd2"/></svg></div>
  <a class="btn upload-btn">UPLOAD NOW</a>
</form>

<section class="hire">
  <h2 class="hire-title">Hire one of our synchro squad to perform at special events.</h2>
  <a class="btn hire-btn">HIRE NOW !</a>
  <div class="hire-divider"></div>
  <div class="event-photo" role="img" aria-label="Photo of three synchro swimmers in red caps at the pool edge"></div>
  <p class="event-date">DECEMBER 2,2016</p>
  <p class="event-meta"><b>Location :</b> New Orleans (USA) &nbsp;<b>Timings</b> 13:00 to 16:00</p>
  <p class="event-text">Neque porro quisquam est qui dolorem ipsum quia dolor sit amet, consectetur...</p>
</section>

<section class="members-band">
  <div class="member-photo young" role="img" aria-label="Photo of two young team swimmers"></div>
  <p class="member-label" style="left:250px">Young</p>
  <h2 class="members-title">Members Only Site</h2>
  <div class="member-photo adult" role="img" aria-label="Photo of two adult team swimmers in swim caps"></div>
  <p class="member-label" style="left:750px">Adult</p>
</section>

<h2 class="section-title" style="top:1580px">News</h2>
<div class="section-rule" style="top:1638px"></div>
<article class="news-card" style="left:202px">
  <div class="news-photo" role="img" aria-label="Video still of a swimmer in the pool"><span class="news-date">DEC<br>2ND<br>2016</span><span class="play"></span></div>
  <h3 class="news-head">Sed ut perspiciatis unde omnis iste natus error sit voluptatem ...</h3>
  <p class="news-body">Sed ut perspiciatis unde omnis iste natus error sit voluptatem accusantium doloremque laudantium, totam rem aperiam, eaque ipsa quae.</p>
</article>
<article class="news-card" style="left:472px">
  <div class="news-photo" role="img" aria-label="Video still of swimmers performing a routine"><span class="news-date">DEC<br>2ND<br>2016</span><span class="play"></span></div>
  <h3 class="news-head">Sed ut perspiciatis unde omnis iste natus error sit voluptatem ...</h3>
  <p class="news-body">Sed ut perspiciatis unde omnis iste natus error sit voluptatem accusantium doloremque laudantium, totam rem aperiam, eaque ipsa quae.</p>
</article>
<article class="news-card" style="left:745px">
  <div class="news-photo" role="img" aria-label="Photo of a team in formation in the pool"><span class="news-date">DEC<br>2ND<br>2016</span></div>
  <h3 class="news-head">Sed ut perspiciatis unde omnis iste natus error sit voluptatem ...</h3>
  <p class="news-body">Sed ut perspiciatis unde omnis iste natus error sit voluptatem accusantium doloremque laudantium, totam rem aperiam, eaque ipsa quae.</p>
</article>

<section class="gear-section">
  <h2 class="section-title" style="top:58px">Buy Logo Gear</h2>
  <div class="section-rule" style="top:120px"></div>
  <div class="gear-card" style="left:202px">
    <div class="gear-photo"><div class="gear-item" role="img" aria-label="Product photo of a green patterned swimsuit" style="background:linear-gradient(180deg,#e7c3a8,#1f8a6e 40%,#0f4f43)"></div></div>
    <p class="gear-name">Coral Tide</p><p class="gear-type">Thin Strap Swimsuit</p><p class="gear-price">$25.95</p>
    <p class="gear-stars">★★★★<span>★</span></p><p class="gear-store">Brindle cove.com</p><a class="btn gear-btn">SHOP NOW</a>
  </div>
  <div class="gear-card" style="left:472px">
    <div class="gear-photo"><div class="gear-item" role="img" aria-label="Product photo of mirrored swim goggles" style="height:60px;width:170px;background:linear-gradient(90deg,#bbb,#eee,#999)"></div></div>
    <p class="gear-name">Clearview Goggles</p><p class="gear-type">Thin Strap Swimsuit</p><p class="gear-price">$15.95</p>
    <p class="gear-stars">★★★★<span>★</span></p><p class="gear-store">Brindle cove.com</p><a class="btn gear-btn">SHOP NOW</a>
  </div>
  <div class="gear-card" style="left:745px">
    <div class="gear-photo"><div class="gear-item" role="img" aria-label="Product photo of a blue swim backpack" style="width:150px;background:linear-gradient(180deg,#3a4fa0,#1f2f6e)"></div></div>
    <p class="gear-name">Swimsuit Bag</p><p class="gear-type">Thin Strap Swimsuit</p><p class="gear-price">$10.95</p>
    <p class="gear-stars">★★★★<span>★</span></p><p class="gear-store">Brindle cove.com</p><a class="btn gear-btn">SHOP NOW</a>
  </div>
</section>

<h2 class="section-title" style="top:2812px">Sponsors</h2>
<div class="sponsor-row">
  <span class="sponsor-name">Brookline</span>
  <span class="sponsor-name">Kestrel</span>
  <span class="sponsor-name">Ridgewell</span>
  <span class="sponsor-name">Tarnby</span>
  <span class="sponsor-name">Quillfare</span>
</div>

<section class="donor-section">
  <h2 class="section-title" style="top:42px">Donated Sponsors</h2>
  <div class="donor" style="left:228px">
    <div class="donor-photo" role="img" aria-label="Portrait of a donor"></div>
    <p class="donor-name">Henry Lavalle</p><p class="donor-team">Reef Runners</p><p class="donor-amount">$55</p>
  </div>
  <div class="donor" style="left:500px">
    <div class="donor-photo" role="img" aria-label="Portrait of a donor"></div>
    <p class="donor-name">Henry Lavalle</p><p class="donor-team">Reef Runners</p><p class="donor-amount">$35</p>
  </div>
  <div class="donor" style="left:772px">
    <div class="donor-photo" role="img" aria-label="Portrait of a donor"></div>
    <p class="donor-name">Henry Lavalle</p><p class="donor-team">Reef Runners</p><p class="donor-amount">$25</p>
  </div>
  <a class="btn sponsor-btn">CLICK HERE TO SPONSOR</a>
</section>

<footer class="site-footer">
  <div class="footer-brand"><span class="brand-mark"></span><span class="brand-name">MARIGOLD</span></div>
  <div class="footer-col footer-about">About us
    <p>At vero eos et accusamus et iusto odio dignissimos ducimus qui blanditiis praesentium voluptatum deleniti atque corrupti quos dolores et quas molestias excepturi sint occaecati.</p>
  </div>
  <div class="footer-col" style="left:625px">Home<br>About us<br>Services<br>Members<br>Schedules<br>Contact us</div>
  <div class="footer-col" style="left:772px">Privacy policy<br>Terms of use<br>Help<br>Disclaimer</div>
  <div class="footer-social"><span class="social-dot"></span><span class="social-dot grey"></span><span class="social-dot grey"></span><span class="social-dot grey"></span></div>
  <div class="calendar-badge"><i></i>Team Calendar</div>
  <div class="footer-rule"></div>
  <p class="copyright">© 2016 COMPANY NAME | ALL RIGHTS RESERVED</p>
</footer>

</body>
</html>
```